Veranix - Solution provider in business consulting

Veranix is a swiss based company providing solutions for developing markets. The business covers various fields of business consulting, such as supply chain, product costs, quality management and manufacturing management. The Business operates in a efficient, straight and solution oriented manner.
The final design should communicate these characteristics. Asian people as well as as western people shall identify the qualities of the company at first sight.
The customer needs business cards with a simple view but an recognizable design, printed in high quality. Engraved elements such as the globe or simple words are possible.
Available colors are: (RAL)
102/102/102
51/102/102
153/204/153
255/102/51
Font: Calibri

```html
<!DOCTYPE html>
<html lang="en">
<head>
<meta charset="utf-8">
<title>Veranix – Business Card</title>
<link rel="stylesheet" href="https://fonts.googleapis.com/css2?family=Carlito:wght@400;700&display=swap">
<style>
  :root {
    --backdrop: #d9d6d0;
    --card-top: #1c1c1c;
    --card-bottom: #050505;
    --ink: #f2f2f2;
    --ink-soft: #bdbdbd;
    --rule: #8a8a8a;
    --globe-tone: #222222;
  }
  * { margin: 0; padding: 0; box-sizing: border-box; }
  html, body {
    width: 1200px; height: 1022px; overflow: hidden;
    background: var(--backdrop);
    font-family: "Carlito", "Calibri", sans-serif;
  }
  .business-card {
    position: absolute; left: 150px; top: 254px;
    width: 900px; height: 514px;
    border-radius: 22px; overflow: hidden;
    background: linear-gradient(160deg, var(--card-top), var(--card-bottom) 70%);
    box-shadow: 0 18px 40px rgba(0,0,0,.35);
    color: var(--ink);
  }
  .globe-decoration {
    position: absolute; left: 500px; top: -110px;
    width: 560px; height: 560px; border-radius: 50%;
    background: radial-gradient(circle at 40% 40%, #2a2a2a, var(--globe-tone) 60%, #121212);
  }
  .brand-name {
    position: absolute; left: 60px; top: 130px;
    font-size: 96px; font-weight: 400; line-height: 1;
    color: var(--ink);
  }
  .divider {
    position: absolute; left: 300px; top: 300px;
    width: 560px; height: 1.5px; background: var(--rule);
  }
  .person {
    position: absolute; right: 40px; top: 222px; text-align: right;
  }
  .person-name { font-size: 34px; font-weight: 700; line-height: 1.1; }
  .person-role { font-size: 19px; color: var(--ink-soft); margin-top: 4px; }
  .address {
    position: absolute; right: 40px; top: 318px; text-align: right;
    font-size: 21px; line-height: 30px; color: var(--ink);
  }
  .contact-list {
    position: absolute; left: 304px; top: 370px;
    list-style: none; font-size: 21px; line-height: 29px; color: var(--ink);
  }
  .contact-list li { display: flex; align-items: center; gap: 12px; }
  .contact-list svg { width: 16px; height: 16px; flex: none; }
</style>
</head>
<body>
  <div class="business-card">
    <div class="globe-decoration" role="img" aria-label="Large faint engraved world globe decoration"></div>

    <span class="brand-name">Veranix</span>

    <div class="person">
      <div class="person-name">Marten Holzer</div>
      <div class="person-role">CEO</div>
    </div>

    <div class="divider"></div>

    <div class="address">
      Veranix GmbH Talstrasse<br>
      14 9200 Nordegg Switzerland
    </div>

    <ul class="contact-list">
      <li>
        <svg viewBox="0 0 18 18" fill="none" stroke="#f2f2f2" stroke-width="1.6"><rect x="5" y="1.5" width="8" height="15" rx="1.5"/><line x1="8" y1="14" x2="10" y2="14"/></svg>
        +41 79 555 0182
      </li>
      <li>
        <svg viewBox="0 0 18 18" fill="#f2f2f2"><path d="M4 2l3 0 1.5 4-2 1.5c1 2 2.5 3.5 4.5 4.5L12.5 10l4 1.5v3c0 1-1 1.5-2 1.5C8 15.5 2.5 10 2.5 3.5 2.5 2.5 3 2 4 2z"/></svg>
        +41 71 555 0347
      </li>
      <li>
        <svg viewBox="0 0 18 18" fill="none" stroke="#f2f2f2" stroke-width="1.6"><rect x="1.5" y="3.5" width="15" height="11" rx="1"/><polyline points="1.5,4 9,10 16.5,4"/></svg>
        marten.holzer@veranix.ch
      </li>
      <li>
        <svg viewBox="0 0 18 18" fill="none" stroke="#f2f2f2" stroke-width="1.4"><circle cx="9" cy="9" r="7.5"/><ellipse cx="9" cy="9" rx="3.2" ry="7.5"/><line x1="1.5" y1="9" x2="16.5" y2="9"/></svg>
        www.veranix.ch
      </li>
    </ul>
  </div>
</body>
</html>
```